Accountant website

Please design a accountant website for www.fenwaybridgeadvisory.com.au. This site is majorly out of date, and is not supported by modern browsers.

The style should use the reds from the design at dev.fenwaybridgeadvisory.com.au, and should be modern and make use of Slides (large content slides that the user scrolls through on the front page).

The content is largely already on the site, however happy to move some around to suit the modern design as required.

The dev.fenwaybridgeadvisory.com.au was a rough mock up that I have completed that the client is "happy" with the direction, however this needs a lot of polish and finishing touches, and I will accept designs that differ from this, but highly recommend that this is used as a guide.

Ready to be sliced PSD Only - HTML no required.

In all honesty, although I can technically do a lot of this, the polished finished I want for this site has eluded me in a few attempts, and therefore I am looking out there at you much more artistic people to finish (or redesign if required) this site.

Target Market(s)

Higher end Small - Medium Business

Industry/Entity Type

Accountant

Requirements
Must have
• Must use the logo from dev.fenwaybridgeadvisory.com.au use exactly the red colours as defined in this layout. A basic layout PSD (to get the colour etc) and the logo in ai format is attached to this project. Please ignore the SSL warning on the development site.

The final product does NOT have to be the same as shown on dev.fenwaybridgeadvisory.com.au however the red colour scheme must be used. The client DOES want the logo on the RIGHT.

Must have a front landing page design, and a page layout that considers the other page content (at least one separate PSD)
Nice to have
• I really am looking at a slide format for the front page simular to:

http://www.quillo.com/au/
http://www.vaultmoor.com/

The attached photos should be used on the site. Was considering a rotating banner with these images are a watermark background on a solid Red header bar, but happy to be shown other options.
Should not have
• Please no "Layout Goblin" submissions.

```html
<!DOCTYPE html>
<html lang="en">
<head>
<meta charset="utf-8">
<title>Fenway Bridge Advisory</title>
<link rel="stylesheet" href="https://fonts.googleapis.com/css2?family=Source+Sans+3:wght@300;400;600;700&display=swap">
<style>
  :root {
    --red: #b52e35;
    --red-deep: #7d1c21;
    --red-text: #b8252c;
    --ink: #333333;
    --muted: #777777;
    --charcoal: #474747;
    --charcoal-dark: #2f2f2f;
    --on-dark: #ffffff;
    --on-dark-muted: #bdbdbd;
    --rule: #e3e3e3;
    --white: #ffffff;
  }
  * { box-sizing: border-box; margin: 0; padding: 0; }
  html, body { width: 1000px; height: 1200px; overflow: hidden; background: var(--white); }
  body { font-family: "Source Sans 3", Arial, sans-serif; color: var(--ink); position: relative; }
  a { color: inherit; text-decoration: none; }

  /* Header */
  .site-header { position: absolute; left: 0; top: 0; width: 1000px; height: 104px; }
  .brand { position: absolute; left: 63px; top: 30px; display: flex; align-items: center; gap: 10px; }
  .brand-mark { width: 14px; height: 14px; background: var(--red); }
  .brand-name { font-weight: 700; font-size: 21px; line-height: 22px; color: var(--ink); text-transform: uppercase; letter-spacing: 0.2px; }
  .main-nav { position: absolute; right: 76px; top: 52px; display: flex; font-size: 16px; text-transform: uppercase; color: #555; }
  .main-nav a { padding: 0 15px; border-left: 1px solid #cfcfcf; line-height: 16px; }
  .main-nav a:first-child { border-left: none; }
  .main-nav a.is-active { color: var(--red-text); }
  .header-rules { position: absolute; left: 0; top: 103px; width: 1000px; height: 10px; border-top: 2px solid var(--red); border-bottom: 2px solid var(--red); }

  /* Hero */
  .hero { position: absolute; left: 0; top: 113px; width: 1000px; height: 403px; background: var(--red); }
  .slider-frame { position: absolute; left: 55px; top: 20px; width: 890px; height: 344px; background: var(--red-deep); padding: 8px; }
  .slide-photo { position: relative; width: 100%; height: 100%;
    background: linear-gradient(180deg, #c93a3f 0%, #a8343a 40%, #d9d4cf 72%, #f1efee 100%); overflow: hidden; }
  .slide-caption { position: absolute; left: 75px; top: 154px; color: var(--white); text-shadow: 0 1px 3px rgba(0,0,0,.45); text-transform: uppercase; }
  .slide-caption .line-1 { font-size: 28px; font-weight: 400; line-height: 32px; letter-spacing: -0.3px; }
  .slide-caption .line-2 { font-size: 33px; font-weight: 700; line-height: 36px; letter-spacing: -0.3px; }
  .slider-arrow { position: absolute; top: 162px; width: 23px; height: 47px; background: var(--red-deep); display: flex; align-items: center; justify-content: center; }
  .slider-arrow.prev { left: 63px; }
  .slider-arrow.next { left: 915px; }
  .slider-dots { position: absolute; top: 374px; left: 0; width: 1000px; display: flex; justify-content: center; gap: 5px; }
  .slider-dots span { width: 13px; height: 13px; border-radius: 50%; background: #d66a6f; }
  .slider-dots span.is-current { background: var(--white); }

  /* Features */
  .features { position: absolute; left: 63px; top: 548px; width: 880px; display: flex; }
  .feature { width: 299px; padding: 0 15px 0 15px; border-left: 1px solid var(--rule); height: 139px; }
  .feature:first-child { border-left: none; padding-left: 15px; }
  .feature:nth-child(2), .feature:nth-child(3) { padding-left: 14px; }
  .feature h2 { font-size: 22px; font-weight: 300; text-transform: uppercase; color: var(--ink); line-height: 26px; margin-top: 5px; }
  .feature h2 strong { font-weight: 600; }
  .feature p { font-size: 13px; font-weight: 300; color: var(--muted); line-height: 20.5px; margin-top: 7px; }
  .learn-link { display: inline-flex; align-items: center; gap: 4px; margin-top: 4px; font-size: 14px; color: var(--red-text); }

  /* Dark band */
  .story { position: absolute; left: 0; top: 721px; width: 1000px; height: 354px; background: var(--charcoal); color: var(--on-dark); }
  .story-main { position: absolute; left: 63px; top: 40px; width: 500px; }
  .story-main .kicker { font-size: 30px; font-weight: 300; line-height: 36px; }
  .story-main h2 { font-size: 34px; font-weight: 400; line-height: 40px; }
  .story-main p { font-size: 13px; font-weight: 300; color: var(--on-dark-muted); line-height: 21.5px; margin-top: 10px; }
  .story-main p + p { margin-top: 8px; }
  .btn-dark { display: inline-block; margin-top: 16px; padding: 6px 16px; background: var(--charcoal-dark); border: 1px solid #3a3a3a; font-size: 14px; color: var(--white); border-radius: 2px; }
  .story-divider { position: absolute; left: 582px; top: 48px; width: 1px; height: 230px; background: #5c5c5c; }
  .articles { position: absolute; left: 613px; top: 45px; width: 340px; }
  .articles h2 { font-size: 27px; font-weight: 400; line-height: 34px; }
  .article { margin-top: 8px; }
  .article + .article { margin-top: 14px; }
  .article h3 { font-size: 16px; font-weight: 400; line-height: 20px; }
  .article p { font-size: 12.5px; font-weight: 300; color: #9a9a9a; line-height: 21.5px; margin-top: 2px; }

  /* Footer */
  .site-footer { position: absolute; left: 0; top: 1075px; width: 1000px; height: 125px; }
  .footer-nav { position: absolute; left: 63px; top: 42px; display: flex; font-size: 15px; text-transform: uppercase; color: #555; }
  .footer-nav a { padding: 0 10px; border-left: 1px solid #999; line-height: 14px; }
  .footer-nav a:first-child { padding-left: 0; border-left: none; }
  .copyright { position: absolute; left: 63px; top: 71px; font-size: 12px; font-weight: 300; color: #666; }
  .partner-badge { position: absolute; left: 626px; top: 38px; width: 49px; height: 49px; border-radius: 50%; background: var(--red); }
  .footer-brand { position: absolute; left: 799px; top: 44px; display: flex; align-items: center; gap: 8px; }
  .footer-brand .brand-name { font-size: 17px; line-height: 18px; }
  .footer-brand .brand-mark { width: 12px; height: 12px; }
</style>
</head>
<body>

<header class="site-header">
  <a class="brand" href="#">
    <span class="brand-name">Fenway Bridge<br>Advisory</span>
    <span class="brand-mark"></span>
  </a>
  <nav class="main-nav">
    <a class="is-active" href="#">Home</a>
    <a href="#">About Us</a>
    <a href="#">Services</a>
    <a href="#">Testimonials</a>
    <a href="#">News</a>
    <a href="#">Contact</a>
  </nav>
  <div class="header-rules"></div>
</header>

<section class="hero">
  <div class="slider-frame">
    <div class="slide-photo" role="img" aria-label="Photo of four smiling consultants seated at a white reception desk in front of a red office wall">
      <div class="slide-caption">
        <div class="line-1">Share your business problems</div>
        <div class="line-2">with our consulting experts</div>
      </div>
    </div>
  </div>
  <a class="slider-arrow prev" href="#" aria-label="Previous slide">
    <svg width="10" height="18" viewBox="0 0 10 18"><path d="M8 1 L2 9 L8 17" fill="none" stroke="#fff" stroke-width="1.6"/></svg>
  </a>
  <a class="slider-arrow next" href="#" aria-label="Next slide">
    <svg width="10" height="18" viewBox="0 0 10 18"><path d="M2 1 L8 9 L2 17" fill="none" stroke="#fff" stroke-width="1.6"/></svg>
  </a>
  <div class="slider-dots"><span class="is-current"></span><span></span><span></span><span></span></div>
</section>

<section class="features">
  <article class="feature">
    <h2>Why <strong>Choose</strong> Us</h2>
    <p>Vamus porttitor, g, purus nisi eleifend libero, a tempus libero lectus feugiat felis. Morbi diam mauris, viverra in, gravida eu</p>
    <a class="learn-link" href="#">Learn More
      <svg width="17" height="17" viewBox="0 0 17 17"><circle cx="8.5" cy="8.5" r="7.5" fill="none" stroke="#b8252c" stroke-width="1.6"/><path d="M4.5 8.5 H10 M8 5.5 L11.5 8.5 L8 11.5" fill="none" stroke="#b8252c" stroke-width="2"/></svg>
    </a>
  </article>
  <article class="feature">
    <h2>How We <strong>Work</strong></h2>
    <p>ivamus porttitor, g, purus nisi eleifend libero, a tempus libero lectus feugiat felis. Morbi diam mauris, viverra in, gravida eu</p>
    <a class="learn-link" href="#">Learn More
      <svg width="17" height="17" viewBox="0 0 17 17"><circle cx="8.5" cy="8.5" r="7.5" fill="none" stroke="#b8252c" stroke-width="1.6"/><path d="M4.5 8.5 H10 M8 5.5 L11.5 8.5 L8 11.5" fill="none" stroke="#b8252c" stroke-width="2"/></svg>
    </a>
  </article>
  <article class="feature">
    <h2><strong>Clients</strong> Success</h2>
    <p>ivamus porttitor, g, purus nisi eleifend libero, a tempus libero lectus feugiat felis. Morbi diam mauris, viverra in, gravida eu</p>
    <a class="learn-link" href="#">Learn More
      <svg width="17" height="17" viewBox="0 0 17 17"><circle cx="8.5" cy="8.5" r="7.5" fill="none" stroke="#b8252c" stroke-width="1.6"/><path d="M4.5 8.5 H10 M8 5.5 L11.5 8.5 L8 11.5" fill="none" stroke="#b8252c" stroke-width="2"/></svg>
    </a>
  </article>
</section>

<section class="story">
  <div class="story-main">
    <div class="kicker">Donec scelerisque leo</div>
    <h2>Luctus dictum eget ferment</h2>
    <p>Phasellus felis dolor, scelerisque a, tempus eget, lobortis id, libero. Donec scelerisque leo ac risus. Praesent sit amet est. In dictum, dolor eu dictum porttitor, enim felis viverra mi, eget luctus massa purus quis odio. Etiam nulla massa, pharetra facilisis, volutpat</p>
    <p>Class aptent taciti sociosqu ad litora torquent per conubia nostra, per inceptos hymenaeos. Proin nulla arcu, nonummy luctus, dictum eget, fermentum et, lorem.</p>
    <a class="btn-dark" href="#">Learn More</a>
  </div>
  <div class="story-divider"></div>
  <div class="articles">
    <h2>Recent Articles</h2>
    <div class="article">
      <h3>Phasellus felis dolor scelerisque</h3>
      <p>Donec scelerisque leo ac risus Praesent sit amet est.</p>
    </div>
    <div class="article">
      <h3>Nunc porta convallis pede</h3>
      <p>Aliquam nec erat at purus cursus interdum Vestibulum ligula</p>
    </div>
    <div class="article">
      <h3>Proin nulla arcu nonummy</h3>
      <p>Phasellus felis dolor, scelerisque a, tempus eget, lobortis id, libero. Donec scelerisque leo ac risus.</p>
    </div>
  </div>
</section>

<footer class="site-footer">
  <nav class="footer-nav">
    <a href="#">Home</a>
    <a href="#">About Us</a>
    <a href="#">Services</a>
    <a href="#">Testimonials</a>
    <a href="#">News</a>
    <a href="#">Contact</a>
  </nav>
  <div class="copyright">© 2013 Company Name.&nbsp; All right reserved.&nbsp; Term of Use</div>
  <div class="partner-badge" role="img" aria-label="Professional accreditation badge"></div>
  <div class="footer-brand">
    <span class="brand-name">Fenway Bridge<br>Advisory</span>
    <span class="brand-mark"></span>
  </div>
</footer>

</body>
</html>
```